Brell Stone Company Business Cards

Front and Back Business Card - logo and text setup - cool design. I need workable photoshop or illustrator files so I can setup each employee card with design that is created
Updates

Hi everyone, thank you for the great entries. Please no more white and blue cards - there are so many already - black and silver only now please. thanks!

Target Market(s)

Construction Industry - Facility Managers

Industry/Entity Type

Construction

Contact Information for Business Card

I really like contemporary simplistic looks - clean neat....not opposed to seeing some black backrounds

Requirements
Must have
• Logo/website address with design on front only - www.brellstone-example.com (logo attached)
• Back:
• Name/Title/Company Address/Phone/email address
Nice to have
• Cool design
Should not have
• Nothing gimmicky like Fire or Water - since we are a Fire Protection company - it has all been done

```html
<!DOCTYPE html>
<html lang="en">
<head>
<meta charset="utf-8">
<title>Brell Stone Company Business Cards</title>
<link rel="stylesheet" href="https://fonts.googleapis.com/css2?family=Open+Sans:wght@400;600;700;800&display=swap">
<style>
  :root {
    --stage: #262626;
    --card-black: #050505;
    --brand-grey: #8c8c8c;
    --url-grey: #d6d6d6;
    --panel-blue: #0a27a0;
    --accent-red: #f0262a;
    --ink-white: #ffffff;
  }
  * { margin: 0; padding: 0; box-sizing: border-box; }
  html, body { width: 1200px; height: 960px; overflow: hidden; }
  body {
    background: var(--stage);
    font-family: "Open Sans", Arial, sans-serif;
    position: relative;
  }
  .card {
    position: absolute;
    left: 250px;
    width: 700px;
    height: 400px;
    background: var(--card-black);
    overflow: hidden;
  }
  .card-front { top: 60px; }
  .card-back { top: 500px; }

  .front-brand {
    position: absolute;
    left: 0; right: 0; top: 118px;
    text-align: center;
    font-weight: 800;
    font-size: 92px;
    letter-spacing: -2px;
    color: var(--brand-grey);
    line-height: 1;
  }
  .front-url {
    position: absolute;
    left: 0; right: 0; top: 262px;
    text-align: center;
    font-size: 17px;
    letter-spacing: 4px;
    color: var(--url-grey);
  }

  .back-panel { position: absolute; inset: 0; }
  .back-brand {
    position: absolute;
    left: 42px; top: 150px;
    font-weight: 800;
    font-size: 56px;
    letter-spacing: -1px;
    line-height: 1;
    color: var(--accent-red);
  }
  .contact {
    position: absolute;
    left: 440px; top: 92px;
    width: 250px;
    color: var(--ink-white);
    font-size: 15px;
    line-height: 1.45;
  }
  .contact-name { font-weight: 700; font-size: 18px; line-height: 1.2; }
  .contact-title { font-size: 16px; margin-bottom: 16px; }
  .contact-list { list-style: none; margin-bottom: 16px; }
  .contact-list li { display: flex; align-items: center; gap: 9px; white-space: nowrap; }
  .contact-list svg { width: 14px; height: 14px; flex: none; }
  .contact-address { font-style: normal; font-size: 15px; }
</style>
</head>
<body>

  <section class="card card-front" aria-label="Card front">
    <div class="front-brand">Brell Stone</div>
    <div class="front-url">www.brellstone-example.com</div>
  </section>

  <section class="card card-back" aria-label="Card back">
    <svg class="back-panel" viewBox="0 0 700 400" width="700" height="400" aria-hidden="true">
      <polygon points="420,0 700,0 700,400 350,400" fill="var(--panel-blue)"/>
      <line x1="420" y1="0" x2="350" y2="400" stroke="var(--accent-red)" stroke-width="4"/>
      <polygon points="398,118 412,106 408,132" fill="var(--accent-red)"/>
    </svg>

    <div class="back-brand">Brell Stone</div>

    <div class="contact">
      <div class="contact-name">Dana Marlow</div>
      <div class="contact-title">President</div>
      <ul class="contact-list">
        <li>
          <svg viewBox="0 0 16 16" aria-hidden="true"><path fill="#fff" d="M3.5 1.5l2.5 0 1 3.5-1.6 1.2a8 8 0 0 0 4.4 4.4L11 9l3.5 1v2.5c0 1-1 2-2 2A11 11 0 0 1 1.5 3.5c0-1 1-2 2-2z"/></svg>
          (555) 014-2270
        </li>
        <li>
          <svg viewBox="0 0 16 16" aria-hidden="true"><rect x="1.5" y="3.5" width="13" height="9" fill="none" stroke="#fff" stroke-width="1.5"/><path d="M1.5 3.5l6.5 5 6.5-5" fill="none" stroke="#fff" stroke-width="1.5"/></svg>
          info@brellstone-example.com
        </li>
        <li>
          <svg viewBox="0 0 16 16" aria-hidden="true"><circle cx="8" cy="8" r="6.5" fill="none" stroke="#fff" stroke-width="1.3"/><ellipse cx="8" cy="8" rx="2.8" ry="6.5" fill="none" stroke="#fff" stroke-width="1.1"/><path d="M1.5 8h13M2.5 5h11M2.5 11h11" stroke="#fff" stroke-width="1"/></svg>
          www.brellstone-example.com
        </li>
      </ul>
      <address class="contact-address">
        48 Harbor Works Road<br>
        Millbrook, NY 10000
      </address>
    </div>
  </section>

</body>
</html>
```